THE LANTERN is a mystical scythian creature, which guarded a golden treasure.

i am a published author back in he 1970's...corvale, edgar fennick, pellam grove. my agent died and the companies have been bought.
i want to publish on my own and have 3 completed novels. DER FROST is the first. i need a book cover, spine and back cover design for the book.
i will use the book design as an important part of a website i am planning for this and the other 2 books. i will need a design for the other books once this is completed.

this book is a thriller; the second is a historical novel, the third is a comedy. i don't know, because of the differing contents whether there should be an consistency in the design. i think not.

i have an excellent Talvern review and will want phrases from it prominently on the design. i like to be involved in the process. although the thriller deals with the Nazis, i don't want a bunch of s.s. officers. I see the book as a labyrinth with almost unbearable twists and turns. it is not a person book, but driven by the PLOT.

the design must be setup for PrintNimbo ( zolvex ) for printing. Font is important.i like black, but not critical.

the Talvern review (below) has an excellent outline and telling of the book.

as the other 2 novels are completed and i need help with a website, this could be more than just one project.

Back Cover Details:
i would like a small photo and 2 line bio next to the photo.on back cover if it fits.... leaving room for the IBSN /barcode.
the cover, design and excerpts are critical for success and i am willing to work and pay extra to have it the best.
i have never done this before as my first 2 novels were published by traditional houses, so, you must forgive any awkwardness in the process.
thank you
+++++++

THIS IS THE TALVERN REVIEW OF THE BOOK::::::::::
DER FROST (THE LANTERN)
Waldbeck, Leonard
Manuscript
BOOK REVIEW
Waldbeck (A Winter of Surgeons, 1983, etc.) offers an animated chase through Boston and Europe as his characters unravel
a mystery involving six pairs of identical Jewish twins saved from a German concentration camp.
In 1965, Henri Castaud, a scientist fruitlessly searching for the secret of telepathy, receives a tantalizing report of
macabre experiments conducted by Otto Wendrich, a Nazi researcher on a similar mission. Castaud searches for the
twins who were the subjects of Wendrich’s experiments, and he gets help from Ilse Varga, the daughter of another
German who was a pawn in a scheme to smuggle unknown items of the collapsing Reich. The first twin they
discover—Greta Mosbach, a woman who had lived a solitary life in a Jewish neighborhood of Boston—is already dead,
the victim of a grisly murder. Her stomach had been sliced open and an odd, smaller tear made in the area of her
appendix. It soon turns out that, not long before her death, Mosbach discovered that she was a beneficiary of a mysterious
will. The search then jumps the Atlantic to England, where Corvin, the powerful company funding Castaud’s research,
pushes Delbury, the bank that served as an executor for the will, to release information on another set of twins—who also
turn out to be dead. The novel’s settings are vivid and refreshingly detailed and include a grotesque concentration camp
in Jena, Germany, as well as the Arcadian French Riviera. The cast of villains is equally colorful, and the story takes
many unexpected turns. Castaud, on the other hand, is a stock protagonist about whom readers learn little more than his
hair color, his profession, and the fact that he enjoys sailing. Corvin, meanwhile, has the convenient ability to coerce
any organization or suspect, but it’s never treated with any scrutiny itself. The novel could also have used a stronger
copy edit; for example, various characters’ thoughts are rendered inconsistently, either in all-caps or underlined. Despite
these issues, however, the overall story is excellent and a reason to look forward to more from this author.
An often audacious Nazi mystery with plenty of well-placed plot twists.

FOR ALL DESIGNERS!!!!!!!!!below is the story of DER FROST, ( THE LANTERN.)FOR THOSE DESIGNERS WHO COULD NOT OPEN THE FILE ON THE CONTEST PAGE.DER FROST (THE LANTERN)Waldbeck, RichardManuscriptBOOK REVIEWHirshhorn (A Winter of Surgeons, 1983, etc.) offers an animated chase through Boston and Europe as his characters unravela mystery involving six pairs of identical Jewish twins saved from a German concentration camp.In 1965, Henri Castaud, a scientist fruitlessly searching for the secret of telepathy, receives a tantalizing report ofmacabre experiments conducted by Otto Wendrich, a Nazi researcher on a similar mission. Castaud searches for thetwins who were the subjects of Wendrich’s experiments, and he gets help from Ilse Varga, the daughter of anotherGerman who was a pawn in a scheme to smuggle unknown items of the collapsing Reich. The first twin theydiscover—Greta Mosbach, a woman who had lived a solitary life in a Jewish neighborhood of Boston—is already dead,the victim of a grisly murder. Her stomach had been sliced open and an odd, smaller tear made in the area of herappendix. It soon turns out that, not long before her death, Mosbach discovered that she was a beneficiary of a mysteriouswill. The search then jumps the Atlantic to England, where Corvin, the powerful company funding Castaud’s research,pushes Delbury, the bank that served as an executor for the will, to release information on another set of twins—who alsoturn out to be dead. The novel’s settings are vivid and refreshingly detailed and include a grotesque concentration campin Jena, Germany, as well as the Arcadian French Riviera. The cast of villains is equally colorful, and the story takesmany unexpected turns. Castaud, on the other hand, is a stock protagonist about whom readers learn little more than hishair color, his profession, and the fact that he enjoys sailing. Corvin, meanwhile, has the convenient ability to coerceany organization or suspect, but it’s never treated with any scrutiny itself. The novel could also have used a strongercopy edit; for example, various characters’ thoughts are rendered inconsistently, either in all-caps or underlined. Despitethese issues, however, the overall story is excellent and a reason to look forward to more from this author.An often audacious Nazi mystery with plenty of well-placed plot twists. Added Tuesday, June 2, 2015

BUDGET NOW $700 !!!!!!! STORY DETAILS NOW UPLOADED TO THE BRIEF.

BUDGET OVER $700 !!!!!!!

adult; males; history buffs; world war II buffs; groups interested in mental telepathy;
people who want their money's worth ona challenging read; people who have faith in the Talvern Reviews.

Sans Serif
• arial.

• front and back cover, spine. a design which grabs enough to want to read back text.
• design to emphasize the puzzle, labyrinth,, riddle, complexity, deceptions, twists, false leads,masquerades,double-dealing, trickiness of the plot.
• presence of identical twins; a treasure.
• the naivety of the american; the duplicities of the germans; the diabolical schemes of the germans. the vulnerability of the children. the ??? suspect mental capability of the identical twins.
• marching nazis,
• ? prominent swastika.
• no horror.
• no supernatural mumbo-jumbo.

```html
<!DOCTYPE html>
<html lang="en">
<head>
<meta charset="utf-8">
<title>DER FROST — Book Jacket</title>
<link rel="stylesheet" href="https://fonts.googleapis.com/css2?family=Arimo:wght@400;700&family=Source+Sans+3:ital,wght@0,400;0,600;1,400;1,600&display=swap">
<style>
  :root {
    --stage: #e6e6e4;
    --red-bright: #e1141b;
    --red-mid: #b50d12;
    --red-deep: #4e0405;
    --ink: #0b0b0b;
    --paper-text: #f7dede;
    --white: #ffffff;
    --disc-light: #efeae2;
    --disc-shade: #a9a195;
    --twin-top: #e2414a;
    --twin-mid: #9a1218;
    --twin-deep: #2e0204;
  }
  * { box-sizing: border-box; margin: 0; padding: 0; }
  html, body { width: 1200px; height: 750px; overflow: hidden; }
  body { background: var(--stage); position: relative; font-family: "Source Sans 3", Arial, sans-serif; }

  .jacket {
    position: absolute; left: 188px; top: 78px;
    width: 824px; height: 594px;
    display: flex;
  }

  /* Back cover */
  .back-cover {
    width: 384px; height: 100%;
    background: linear-gradient(180deg, var(--red-bright) 0%, var(--red-mid) 40%, var(--red-deep) 100%);
    padding: 16px 10px 0 22px;
    color: var(--paper-text);
  }
  .review-source {
    text-align: center; font-size: 10.5px; line-height: 13.2px;
    text-transform: uppercase; color: var(--white);
  }
  .review-source__name {
    display: inline-flex; align-items: center; gap: 6px;
    margin-bottom: 4px; margin-left: -4px;
  }
  .review-source__mark { width: 10px; height: 10px; background: var(--white); flex: none; }
  .review-source__words {
    font-size: 19px; line-height: 20px; font-weight: 600; letter-spacing: 0.6px;
    color: var(--white); text-align: left;
  }
  .review-source__author { font-style: italic; font-weight: 600; text-transform: none; }
  .review-source__kind { text-transform: none; }
  .review-text {
    margin-top: 24px; font-size: 10.9px; line-height: 13.5px;
    text-align: justify; color: var(--paper-text);
  }
  .review-text + .review-text { margin-top: 13.5px; }

  /* Spine */
  .spine {
    width: 46px; height: 100%;
    background: linear-gradient(180deg, var(--red-bright) 0%, var(--red-mid) 55%, var(--red-deep) 100%);
    position: relative;
  }
  .spine__title, .spine__author {
    position: absolute; left: 50%;
    writing-mode: vertical-rl; transform: translateX(-50%);
    font-family: "Arimo", Arial, sans-serif; white-space: nowrap;
  }
  .spine__title { top: 32px; font-size: 25px; font-weight: 700; letter-spacing: 9px; color: var(--ink); }
  .spine__author { top: 312px; font-size: 14px; letter-spacing: 6.5px; color: var(--white); }

  /* Front cover */
  .front-cover {
    width: 394px; height: 100%; position: relative; overflow: hidden;
    background: linear-gradient(180deg, var(--red-bright) 0%, var(--red-mid) 60%, var(--red-deep) 100%);
  }
  .front-cover__emblem { position: absolute; left: 8px; top: 32px; }
  .front-cover__title {
    position: absolute; top: 28px; left: 0; width: 100%; text-align: center;
    font-family: "Arimo", Arial, sans-serif; font-weight: 700; white-space: nowrap;
    font-size: 42px; line-height: 50px; letter-spacing: 12px; color: var(--ink);
    padding-left: 12px;
  }
  .front-cover__twins {
    position: absolute; left: 0; bottom: 0; width: 100%; height: 212px;
    background: linear-gradient(180deg, var(--twin-top) 0%, var(--twin-mid) 40%, var(--twin-deep) 100%);
  }
  .front-cover__author {
    position: absolute; top: 479px; left: 0; width: 100%; text-align: center;
    font-family: "Arimo", Arial, sans-serif; font-size: 17.5px; white-space: nowrap;
    letter-spacing: 5.2px; color: var(--white); padding-left: 5px;
  }
</style>
</head>
<body>
  <main class="jacket">
    <section class="back-cover">
      <header class="review-source">
        <div class="review-source__name">
          <span class="review-source__mark"></span>
          <span class="review-source__words">TALVERN<br>REVIEWS</span>
        </div>
        <p>OF THE BOOK</p>
        <p>DER FROST (THE LANTERN)</p>
        <p class="review-source__author">Waldbeck, Leonard</p>
        <p class="review-source__kind">Manuscript</p>
        <p>BOOK REVIEW</p>
      </header>
      <p class="review-text">Waldbeck (A Winter of Surgeons, 1983, etc.) offers an animated chase through Boston and Europe as his characters unravel a mystery involving six pairs of identical Jewish twins saved from a German concentration camp. In 1965, Henri Castaud, a scientist fruitlessly searching for the secret of telepathy, receives a tantalizing report of macabre experiments conducted by Otto Wendrich, a Nazi researcher on a similar mission. Castaud searches for the twins who were the subjects of Wendrich’s experiments, and he gets help from Ilse Varga, the daughter of another German who was a pawn in a scheme to smuggle unknown items of the collapsing Reich. The first twin they discover—Greta Mosbach, a woman who had lived a solitary life in a Jewish neighborhood of Boston—is already dead, the victim of a grisly murder. Her stomach had been sliced open and an odd, smaller tear made in the area of her appendix. It soon turns out that, not long before her death, Mosbach discovered that she was a beneficiary of a mysterious</p>
      <p class="review-text">will. The search then jumps the Atlantic to England, where Corvin, the powerful company funding Castaud’s research, pushes Delbury, the bank that served as an executor for the will, to release information on another set of twins—who also turn out to be dead. The novel’s settings are vivid and refreshingly detailed and include a grotesque concentration camp in Jena, Germany, as well as the Arcadian French Riviera. The cast of villains is equally colorful, and the story takes many unexpected turns. Castaud, on the other hand, is a stock protagonist about whom readers learn little more than his hair color, his profession, and the fact that he enjoys sailing. Corvin, meanwhile, has the convenient ability to coerce any organization or suspect, but it’s never treated with any scrutiny itself. The novel could also have used a stronger copy edit; for example, various characters’ thoughts are rendered inconsistently, either in all-caps or underlined. Despite these issues, however, the overall story is excellent and a reason to look forward to more from this author. An often audacious Nazi mystery with plenty of well-placed plot twists.</p>
    </section>

    <section class="spine">
      <span class="spine__title">DER FROST</span>
      <span class="spine__author">LEONARD WALDBECK</span>
    </section>

    <section class="front-cover">
      <svg class="front-cover__emblem" width="380" height="380" viewBox="0 0 380 380" role="img" aria-label="Cover emblem: a pale stone disc bearing a wartime insignia with a mythical creature and a dagger">
        <defs>
          <radialGradient id="disc-tone" cx="42%" cy="38%" r="65%">
            <stop offset="0%" stop-color="var(--disc-light)"/>
            <stop offset="100%" stop-color="var(--disc-shade)"/>
          </radialGradient>
        </defs>
        <circle cx="190" cy="190" r="189" fill="url(#disc-tone)"/>
      </svg>
      <h1 class="front-cover__title">DER FROST</h1>
      <div class="front-cover__twins" role="img" aria-label="A row of identical twin children in red-tinted tones along the lower cover"></div>
      <p class="front-cover__author">LEONARD WALDBECK</p>
    </section>
  </main>
</body>
</html>
```